Tech business card design

We need an amazing business card design for our new business 'Pexla' a marketing tech startup based in Sydney, Australia. We provide an online marketplace for businesses to search and buy advertising media, connect with service providers and learn more about marketing. We wish to communicate 'cool tech', reliability and professionalism and design based around our logo.

Target Market(s)

Business Owners

Contact Information for Business Card

Name
Position
Email Address
Website
Phone Number

Font styles to use
Other font styles liked:
• Avenir & Avenir Next

Colors

Designer to choose colors to be used in the design.

```html
<!DOCTYPE html>
<html lang="en">
<head>
<meta charset="utf-8">
<title>Pexla Business Card</title>
<link href="https://fonts.googleapis.com/css2?family=Montserrat:wght@400;500;700;800&display=swap" rel="stylesheet">
<style>
  :root {
    --backdrop: #1e1d1c;
    --navy: #1d2150;
    --navy-deep: #181c45;
    --paper: #ffffff;
    --ink: #1a1a24;
    --ghost: #676b93;
  }
  * { margin: 0; padding: 0; box-sizing: border-box; }
  html, body { width: 1200px; height: 900px; overflow: hidden; }
  body {
    background: var(--backdrop);
    font-family: "Montserrat", sans-serif;
    position: relative;
  }
  .card {
    position: absolute;
    width: 520px;
    height: 300px;
    border-radius: 26px;
    overflow: hidden;
    box-shadow: 0 14px 30px rgba(0,0,0,0.55);
  }
  .card-front { left: 110px; top: 120px; background: var(--paper); }
  .card-back { left: 570px; top: 480px; background: var(--navy-deep); }
  .front-wave { position: absolute; inset: 0; width: 100%; height: 100%; }
  .brand-name {
    position: absolute;
    left: 40px; top: 30px;
    font-weight: 800;
    font-size: 78px;
    letter-spacing: -1px;
    color: var(--navy);
    line-height: 1;
  }
  .contact-list {
    position: absolute;
    left: 96px; top: 134px;
    list-style: none;
    font-size: 13px;
    color: var(--ink);
    line-height: 1.55;
  }
  .contact-list li { display: flex; align-items: center; gap: 6px; }
  .contact-list svg { width: 12px; height: 12px; fill: none; stroke: var(--ink); stroke-width: 1.6; }
  .address {
    position: absolute;
    left: 112px; top: 204px;
    font-size: 13px;
    color: var(--ink);
    line-height: 1.3;
  }
  .holder {
    position: absolute;
    right: 28px; top: 222px;
    text-align: right;
    color: var(--paper);
    white-space: nowrap;
  }
  .holder-name { font-weight: 700; font-size: 15px; letter-spacing: 0.3px; }
  .holder-role { font-weight: 500; font-size: 12px; }
  .back-name {
    position: absolute;
    inset: 0;
    display: flex;
    align-items: center;
    justify-content: center;
    font-weight: 800;
    font-size: 130px;
    letter-spacing: -2px;
    color: var(--ghost);
  }
</style>
</head>
<body>
  <section class="card card-front">
    <svg class="front-wave" viewBox="0 0 520 300" preserveAspectRatio="none" aria-hidden="true">
      <path d="M0,205 C80,230 130,290 230,288 C320,286 360,150 520,140 L520,300 L0,300 Z" fill="var(--navy)"/>
      <path d="M220,296 C330,294 380,168 520,156" fill="none" stroke="var(--paper)" stroke-width="3"/>
      <path d="M300,196 C370,150 440,130 520,126" fill="none" stroke="var(--navy)" stroke-width="3"/>
    </svg>
    <div class="brand-name">Pexla</div>
    <ul class="contact-list">
      <li>
        <svg viewBox="0 0 12 12"><path d="M2,1.5 L4.5,1.5 L5.2,4 L3.8,5 C4.5,6.6 5.4,7.5 7,8.2 L8,6.8 L10.5,7.5 L10.5,10 C6,10 2,6 2,1.5 Z"/></svg>
        012-345-6789
      </li>
      <li>
        <svg viewBox="0 0 12 12"><rect x="1" y="2.5" width="10" height="7"/><path d="M1,2.5 L6,6.5 L11,2.5"/></svg>
        info@pexla.com
      </li>
      <li>
        <svg viewBox="0 0 12 12"><circle cx="6" cy="6" r="4.8"/><path d="M1.2,6 H10.8 M6,1.2 C3.5,4 3.5,8 6,10.8 M6,1.2 C8.5,4 8.5,8 6,10.8"/></svg>
        www.pexla.com
      </li>
    </ul>
    <p class="address">Street Name, City Name<br>Zipcode:012345</p>
    <div class="holder">
      <p class="holder-name">JOHN SMITH</p>
      <p class="holder-role">Position</p>
    </div>
  </section>

  <section class="card card-back">
    <div class="back-name">Pexla</div>
  </section>
</body>
</html>
```